Business Card Design Project

I have a two letter domain name zu.com.au (lower case font please). I want a business card, cum logo that is die cut (around the zu segment at least) that fits standard business card size.
zu is all about what 'I am' - a journalist, blogger, analyst, commentator. My mantra is "I think therefore zu'.
The reverse of the card only needs my name Olin Verka, email olin@zu.com.au and mobile +61 437 185 923
Mainly people that will use my professional writing services and suppliers that will provide product for review
Business
- One side is zu.com.au (hint - the .com.au can be vertical or horizontal to fit - the zu should be as large as possible).
The other requires large size font name, email and phone details (so no one needs glasses to read it).
The die cut can be just to highlight the zu segment - need not be around the whole card.
Font used in the past was Belwe (old style - very much like the i used in the information symbol).
Colours - no preference - prefer two colour to process colour but can also be an outline font instead of solid colour.

```html
<!DOCTYPE html>
<html lang="en">
<head>
<meta charset="utf-8">
<title>zu.com.au business cards</title>
<link rel="stylesheet" href="https://fonts.googleapis.com/css2?family=Gelasio:wght@400;700&display=swap">
<style>
  :root {
    --page: #f6f6f6;
    --card-light: #fbfbfb;
    --card-dark: #3a3a3a;
    --accent: #1ea3e0;
    --cut-light: #dedede;
    --cut-dark: #ffffff;
    --text-light: #f2f2f2;
    --text-muted: #cfcfcf;
    --band: #9d9d9d;
    --band-text: #2a2a2a;
    --domain-muted: #8a8a8a;
  }
  * { margin: 0; padding: 0; box-sizing: border-box; }
  html, body { width: 1200px; height: 949px; overflow: hidden; }
  body {
    position: relative;
    background: var(--page);
    font-family: "Gelasio", Georgia, serif;
  }
  .card { position: absolute; border-radius: 10px; overflow: hidden; }
  .card--light { background: var(--card-light); width: 393px; height: 224px; top: 72px; }
  .card--dark { background: var(--card-dark); width: 224px; height: 393px; top: 473px; }
  .card--front-light { left: 157px; }
  .card--back-light { left: 660px; }
  .card--front-dark { left: 327px; }
  .card--back-dark { left: 661px; }

  .wordmark {
    position: absolute;
    font-weight: 700;
    font-size: 132px;
    line-height: 1;
    letter-spacing: -2px;
  }
  .wordmark--mirrored { transform: scaleX(-1); }
  .card--light .wordmark { color: var(--cut-light); }
  .card--dark .wordmark { color: var(--cut-dark); }

  .card--front-light .wordmark { left: 108px; top: 50px; }
  .card--back-light .wordmark { left: 127px; top: 50px; }
  .card--front-dark .wordmark { left: 26px; top: 42px; }
  .card--back-dark .wordmark { left: 40px; top: 42px; }

  .domain-suffix {
    position: absolute;
    font-size: 15px;
    line-height: 1;
    transform-origin: left top;
    transform: rotate(90deg);
    white-space: nowrap;
  }
  .card--front-light .domain-suffix { color: var(--accent); left: 291px; top: 80px; }
  .card--front-dark .domain-suffix { color: var(--domain-muted); left: 202px; top: 68px; }

  .contact-name { font-weight: 700; font-size: 19px; line-height: 1; }
  .contact-line { font-size: 18px; line-height: 1; }

  .card--back-light .contact {
    position: absolute; left: 0; right: 0; top: 170px;
    text-align: center; color: var(--accent);
  }
  .card--back-light .contact-line { margin-top: 8px; }
  .divider { margin: 0 8px; }

  .card--front-dark .contact {
    position: absolute; left: 24px; top: 302px; color: var(--text-light);
  }
  .card--front-dark .contact-name { margin-left: 32px; margin-bottom: 9px; }
  .contact-row { display: flex; align-items: center; margin-top: 8px; }
  .contact-icon { width: 32px; display: flex; align-items: center; }

  .roles {
    position: absolute; right: 30px; top: 192px;
    list-style: none; text-align: right;
    color: var(--text-muted); font-size: 18px; line-height: 30px;
  }
  .mantra-band {
    position: absolute; left: 0; right: 0; top: 325px; height: 44px;
    background: var(--band); color: var(--band-text);
    text-align: right; padding: 4px 30px 0 0;
    font-size: 13px; line-height: 15px;
  }
</style>
</head>
<body>
  <section class="card card--light card--front-light" aria-label="Light card front">
    <span class="wordmark">zu</span>
    <span class="domain-suffix">.com.au</span>
  </section>

  <section class="card card--light card--back-light" aria-label="Light card back">
    <span class="wordmark wordmark--mirrored">zu</span>
    <div class="contact">
      <p class="contact-name">Olin Verka</p>
      <p class="contact-line">olin@zu.com.au<span class="divider">|</span>+61 437 185 923</p>
    </div>
  </section>

  <section class="card card--dark card--front-dark" aria-label="Dark card front">
    <span class="wordmark">zu</span>
    <span class="domain-suffix">.com.au</span>
    <div class="contact">
      <p class="contact-name">Olin Verka</p>
      <p class="contact-row contact-line">
        <span class="contact-icon">
          <svg width="12" height="9" viewBox="0 0 12 9" aria-hidden="true">
            <rect x="0" y="0" width="12" height="9" fill="#e8e8e8"/>
            <path d="M0 0 L6 5 L12 0" fill="none" stroke="#3a3a3a" stroke-width="1.2"/>
          </svg>
        </span>olin@zu.com.au
      </p>
      <p class="contact-row contact-line">
        <span class="contact-icon">
          <svg width="10" height="15" viewBox="0 0 10 15" aria-hidden="true">
            <rect x="0.75" y="0.75" width="8.5" height="13.5" rx="1.5" fill="none" stroke="#e8e8e8" stroke-width="1.5"/>
            <rect x="3" y="11" width="4" height="1.4" fill="#e8e8e8"/>
          </svg>
        </span>+61 437 185 923
      </p>
    </div>
  </section>

  <section class="card card--dark card--back-dark" aria-label="Dark card back">
    <span class="wordmark wordmark--mirrored">zu</span>
    <ul class="roles">
      <li>analyst</li>
      <li>blogger</li>
      <li>journalist</li>
      <li>commentator</li>
    </ul>
    <div class="mantra-band">
      <p>"I think therefore zu"</p>
      <p>zu.com.au</p>
    </div>
  </section>
</body>
</html>
```